Law Offices business card

Hi there, I'll need business card for the Law Offices of Colin Matheny. The information must convey his strategic approach and quick resolution to complex business litigation needs. Please emphasize Civil Litigation, Corporate Law, Business Governance and Real Estate Law. Colin has over 25 years of experience in these fields.The card should be modern and edgy and the message should be clear. Please consult his current website for ideas.

```html
<!DOCTYPE html>
<html lang="en">
<head>
<meta charset="utf-8">
<title>Law Offices of Colin Matheny – Business Card</title>
<link rel="stylesheet" href="https://fonts.googleapis.com/css2?family=Cinzel:wght@400;500&family=Source+Sans+3:wght@400;600;700&display=swap">
<style>
  :root {
    --backdrop: #1c1c1c;
    --card: #ffffff;
    --accent: #ec7a2a;
    --ink: #141414;
    --text: #333333;
  }
  * { margin: 0; padding: 0; box-sizing: border-box; }
  html, body { width: 1200px; height: 900px; overflow: hidden; }
  body {
    background: var(--backdrop);
    position: relative;
    font-family: "Source Sans 3", Arial, sans-serif;
    color: var(--text);
  }
  .card {
    position: absolute;
    top: 170px;
    width: 347px;
    height: 561px;
    background: var(--card);
    text-align: center;
  }
  .card--front { left: 259px; }
  .card--back { left: 631px; }

  .accent-bar {
    position: absolute;
    left: 102px;
    width: 143px;
    background: var(--accent);
  }
  .accent-bar--top { top: 0; height: 30px; }
  .accent-bar--bottom { bottom: 0; height: 28px; }

  .brand-mark {
    position: absolute;
    left: 0; right: 0;
    display: flex;
    flex-direction: column;
    align-items: center;
    color: var(--ink);
    font-family: "Cinzel", Georgia, serif;
    font-weight: 500;
  }
  .brand-mark__circle {
    border: 3px solid var(--ink);
    border-radius: 50%;
  }
  .card--front .brand-mark { top: 84px; gap: 8px; font-size: 14px; letter-spacing: 1px; }
  .card--front .brand-mark__circle { width: 58px; height: 58px; }
  .card--back .brand-mark { top: 84px; gap: 18px; font-size: 26px; letter-spacing: 2px; }
  .card--back .brand-mark__circle { width: 170px; height: 170px; border-width: 6px; }

  .firm-name {
    position: absolute;
    top: 191px; left: 0; right: 0;
    font-family: "Cinzel", Georgia, serif;
    font-weight: 400;
  }
  .firm-name__line1 { display: block; color: var(--accent); font-size: 27px; letter-spacing: 1.5px; line-height: 30px; }
  .firm-name__line2 { display: block; color: var(--ink); font-size: 19px; line-height: 24px; margin-top: 2px; }

  .person { position: absolute; top: 279px; left: 0; right: 0; }
  .person__name { color: var(--accent); font-weight: 600; font-size: 21px; line-height: 26px; }
  .person__title { font-size: 15px; line-height: 18px; color: var(--text); }

  .address { position: absolute; top: 334px; left: 0; right: 0; font-size: 16px; line-height: 20px; font-style: normal; }

  .contacts { position: absolute; top: 385px; left: 0; right: 0; list-style: none; font-size: 16px; }
  .contacts li { height: 23.5px; display: flex; justify-content: center; align-items: center; gap: 7px; }
  .contacts svg { width: 12px; height: 12px; fill: var(--accent); }

  .practice-areas {
    position: absolute;
    top: 370px; left: 0; right: 0;
    list-style: none;
    color: var(--ink);
    font-weight: 600;
    font-size: 18px;
    line-height: 25px;
  }
</style>
</head>
<body>
  <section class="card card--front" aria-label="Business card front">
    <div class="accent-bar accent-bar--top"></div>
    <div class="brand-mark">
      <span class="brand-mark__circle"></span>
      <span class="brand-mark__name">Matheny Legal</span>
    </div>
    <h1 class="firm-name">
      <span class="firm-name__line1">Law Offices</span>
      <span class="firm-name__line2">Of Colin Matheny</span>
    </h1>
    <div class="person">
      <p class="person__name">Colin Matheny</p>
      <p class="person__title">Attorney</p>
    </div>
    <address class="address">
      318B Harbor Lane<br>Coral Point, Florida 33412
    </address>
    <ul class="contacts">
      <li><svg viewBox="0 0 12 12"><path d="M2.5 0.5l2 2.5-1.2 1.4c.7 1.6 2 2.9 3.4 3.6L8 6.8l2.7 2-1 2.4C5 11 0.8 6.6 0.6 2z"/></svg>561-555-0184</li>
      <li><svg viewBox="0 0 12 12"><path d="M3 0h5l1.5 1.5V4H11v8H1V4h2zM4 1v3h4.5V2H7.5V1zM3 6v1h2V6zm3 0v1h2V6zM3 8v1h2V8zm3 0v1h2V8z"/></svg>561-555-0197</li>
      <li><svg viewBox="0 0 12 12"><path d="M0 2h12v1.2L6 7 0 3.2zM0 4.6l6 3.8 6-3.8V10H0z"/></svg>colin@mathenylegal.com</li>
      <li><svg viewBox="0 0 12 12"><path d="M6 0a6 6 0 1 0 0 12A6 6 0 0 0 6 0zm-1 2.5c1 .5 1.8 1.2 1.5 2.2-.3.8-1.7.4-2 1.4-.2.9 1 1.4.6 2.6-.3.8-1.5.9-2.3.4A4.5 4.5 0 0 1 5 2.5zm3 3.3c.9-.3 1.9.2 2.4 1a4.5 4.5 0 0 1-2 2.8c-.4-1.1-1.2-2.9-.4-3.8z"/></svg>www.mathenylegal.com</li>
    </ul>
    <div class="accent-bar accent-bar--bottom"></div>
  </section>

  <section class="card card--back" aria-label="Business card back">
    <div class="brand-mark">
      <span class="brand-mark__circle"></span>
      <span class="brand-mark__name">Matheny Legal</span>
    </div>
    <ul class="practice-areas">
      <li>Civil Litigation</li>
      <li>Corporate Law</li>
      <li>Business Governance</li>
      <li>Real Estate Law</li>
    </ul>
  </section>
</body>
</html>
```